Harwick Moss Fine Art gallery website - Modern british art for sale

We need a website design that is both current and high end. Our products are expensive and this should be reflected in the look of the website. We would like the logo we had designed last year to be clearly seen in the design. We want sleek, simple, and easy to navigate. Nothing too colourful as the colours of the art should always take precedence.

Target Market(s)

The average price of one our products starts at £250 and can go up to £10,000 we are an entry level gallery.

Industry/Entity Type

Art Gallery

Number of Pages Required

5+ page

Font styles to use
Sans Serif

Colors
000000
ffffff
faa54b
abd037
886aae
b868aa

Requirements
Must have
• Attractive front page. Linked to our Chirpline feed.
• 4 links from front page - New Releases, about us, Artists, contact us
• Social media links - Facebook, Chirpline, YouTube, Instagram.
• Each artist must have their own page, each page must have a biography link to another page.
Nice to have
• Utilise our new logo design. I would like the Chirpline feed to link to the front page in a small way so you can see what's being said on Chirpline by the company. For future proofing maybe have a locations function on the front page which can be adroit down menu showing where our other galleries are.

```html
<!DOCTYPE html>
<html lang="en">
<head>
<meta charset="utf-8">
<title>Harwick Moss Fine Art</title>
<link href="https://fonts.googleapis.com/css2?family=Raleway:wght@400;500;600&family=Open+Sans:wght@400;600;700&display=swap" rel="stylesheet">
<style>
:root{
  --ink:#222222;
  --text:#3a3a3a;
  --muted:#8a8a8a;
  --line:#dcdcdc;
  --white:#ffffff;
  --purple:#886aae;
  --orange:#faa54b;
  --green:#abd037;
  --pink:#b868aa;
  --footer-bg:#efefef;
  --card-bg:#f3f3f3;
  --sky:#3fb6e6;
}
*{box-sizing:border-box;margin:0;padding:0}
html,body{width:1200px;height:2270px;overflow:hidden}
body{position:relative;background:var(--white);font-family:"Open Sans",Arial,sans-serif;color:var(--text)}
.abs{position:absolute}

/* header */
.site-header{left:0;top:0;width:1200px;height:106px;border-bottom:1px solid var(--line);background:var(--white)}
.brand{left:160px;top:40px;display:flex;align-items:center;gap:10px}
.brand-dot{width:14px;height:14px;border-radius:50%;background:var(--sky)}
.brand-name{font-family:"Raleway",Arial,sans-serif;font-weight:500;font-size:25px;letter-spacing:1px;color:var(--ink);text-transform:uppercase}
.utility{right:160px;top:20px;display:flex;align-items:center;gap:8px;font-size:12px;color:var(--text)}
.utility .sep{color:#bbb}
.main-nav{right:160px;top:68px;display:flex;gap:31px;font-family:"Raleway",Arial,sans-serif;font-size:13px;font-weight:500;text-transform:uppercase;color:var(--ink)}
.main-nav .active{color:var(--purple)}

/* hero */
.hero{left:0;top:106px;width:1200px;height:537px;overflow:hidden}
.hero-art{position:absolute;inset:0;background:
  radial-gradient(ellipse 420px 300px at 1050px 120px,#6b3f9e 0%,rgba(107,63,158,0) 70%),
  radial-gradient(ellipse 380px 260px at 1000px 380px,#d9562e 0%,rgba(217,86,46,0) 70%),
  radial-gradient(ellipse 360px 280px at 720px 260px,#9b7cc4 0%,rgba(155,124,196,0) 70%),
  linear-gradient(90deg,#f2ede6 0%,#efe8e0 40%,#c9b4d8 65%,#7a52a8 100%)}
.hero-title{left:160px;top:208px;font-family:"Raleway",Arial,sans-serif;font-weight:600;font-size:46px;line-height:1.05;text-transform:uppercase}
.hero-title .accent{color:var(--purple);display:block}
.hero-title .main{color:var(--ink);display:block}
.slider-dots{left:568px;top:492px;display:flex;gap:4px}
.slider-dots span{width:12px;height:12px;border-radius:50%;background:#7d7d7d}
.slider-dots span.on{background:var(--orange)}

/* category tiles */
.tile{top:675px;width:275px;height:193px;overflow:hidden}
.tile-art{position:absolute;inset:0}
.tile-label{position:absolute;top:101px;right:0;height:56px;color:var(--white);text-align:center;padding-top:7px;padding-left:22px;clip-path:polygon(14px 0,100% 0,100% 100%,0 100%)}
.tile-label b{display:block;font-family:"Raleway",Arial,sans-serif;font-weight:600;font-size:16px}
.tile-label small{display:block;font-size:11.5px;font-weight:600}
.tile-trending{left:162px}.tile-trending .tile-art{background:linear-gradient(135deg,#8a5a2f,#57b3a4 45%,#c47b3a 80%)}
.tile-trending .tile-label{background:var(--orange);width:202px}
.tile-collection{left:462px}.tile-collection .tile-art{background:linear-gradient(120deg,#f06a3a,#b67fd0 35%,#cdb94a 60%,#f06a3a 85%)}
.tile-collection .tile-label{background:var(--purple);width:208px}
.tile-prints{left:763px}.tile-prints .tile-art{background:linear-gradient(120deg,#e8dcd6,#c8bfbd 50%,#f0e4e7)}
.tile-prints .tile-label{background:var(--green);width:205px}

/* sections */
.section-title{left:0;width:1200px;text-align:center;font-family:"Raleway",Arial,sans-serif;font-weight:500;font-size:26px;color:var(--ink)}
.product{width:275px;height:264px;background:var(--card-bg)}
.product-art{height:191px}
.product-name{text-align:center;font-family:"Raleway",Arial,sans-serif;font-weight:500;font-size:15px;color:var(--ink);margin-top:18px}
.product-price{text-align:center;font-size:12px;font-weight:700;color:var(--purple);margin-top:5px}
.btn-more{left:505px;top:1569px;width:190px;height:38px;background:var(--orange);color:var(--white);font-size:12px;font-weight:600;text-transform:uppercase;text-align:center;line-height:38px}
.divider{left:162px;top:1652px;width:878px;height:1px;background:var(--line)}

/* feed */
.post{top:1743px;width:420px;display:flex;gap:14px}
.post-mark{width:22px;height:22px;border-radius:50%;background:var(--sky);flex:none}
.post-head{font-size:12.5px;color:var(--muted)}
.post-head b{color:var(--ink);font-weight:700}
.post-body{font-size:12px;line-height:19px;color:var(--text);margin-top:4px}
.post-meta{display:flex;gap:22px;margin-top:14px;font-size:12px;color:var(--text);align-items:center}
.post-meta svg{vertical-align:-2px;margin-right:5px}

/* footer */
.site-footer{left:0;top:1909px;width:1200px;height:361px;background:var(--footer-bg);border-top:2px solid var(--purple)}
.f-col{top:42px}
.f-col h4{font-family:"Raleway",Arial,sans-serif;font-weight:600;font-size:14px;color:var(--ink);margin-bottom:16px}
.f-col ul{list-style:none}
.f-col li{font-size:11px;line-height:19.5px;color:var(--text)}
.newsletter{display:flex;margin-top:4px}
.newsletter .field{width:220px;height:35px;background:var(--white);border:1px solid #d5d5d5;font-size:10px;font-style:italic;padding:11px 14px;color:var(--text)}
.newsletter .go{width:73px;height:35px;background:var(--purple);color:var(--white);font-size:11px;font-weight:700;text-align:center;line-height:35px}
.social{display:flex;gap:7px;margin-top:10px}
.social span{width:20px;height:20px;border-radius:50%;border:1px solid #555}
.legal-rule{left:162px;top:291px;width:878px;height:1px;background:#d8d8d8}
.legal{left:0;top:312px;width:1200px;text-align:center;font-size:11px;color:var(--ink)}
.legal .sep{margin:0 9px}
</style>
</head>
<body>

<header class="site-header abs">
  <div class="brand abs"><span class="brand-dot"></span><span class="brand-name">Harwick Moss Fine Art</span></div>
  <div class="utility abs">
    <svg width="11" height="13" viewBox="0 0 11 13"><rect x="1" y="3" width="9" height="9" fill="none" stroke="#555"/><path d="M3.5 3V1.5h4V3" fill="none" stroke="#555"/></svg>
    <span class="sep">|</span>
    <svg width="14" height="12" viewBox="0 0 14 12"><path d="M7 11 1.5 5.5A3 3 0 0 1 7 2a3 3 0 0 1 5.5 3.5Z" fill="none" stroke="#555"/></svg>
    <span class="sep">|</span>
    <svg width="13" height="13" viewBox="0 0 13 13"><circle cx="6.5" cy="6.5" r="6" fill="#c8c8d8" stroke="#999"/></svg>
    <span class="sep">|</span><span>Gift Cards</span><span class="sep">|</span><span>Sign In</span>
  </div>
  <nav class="main-nav abs">
    <span class="active">Home</span><span>New Releases</span><span>About Us</span><span>Artists</span><span>Contact Us</span>
    <svg width="12" height="12" viewBox="0 0 12 12"><circle cx="5" cy="5" r="3.5" fill="none" stroke="#222" stroke-width="1.6"/><path d="M7.6 7.6 11 11" stroke="#222" stroke-width="1.6"/></svg>
  </nav>
</header>

<section class="hero abs">
  <div class="hero-art" role="img" aria-label="Splashes of purple, orange and blue paint on crumpled paper with two framed art prints"></div>
  <h1 class="hero-title abs"><span class="accent">Harwick Moss</span><span class="main">Fineart Print</span></h1>
  <div class="slider-dots abs"><span></span><span></span><span></span><span class="on"></span></div>
</section>

<a class="tile tile-trending abs"><div class="tile-art" role="img" aria-label="Intricate teal and brown patterned artwork"></div><div class="tile-label"><b>Trending Now</b><small>View More Products</small></div></a>
<a class="tile tile-collection abs"><div class="tile-art" role="img" aria-label="Abstract orange, lilac and olive wave print"></div><div class="tile-label"><b>Fineart Collection</b><small>View More Products</small></div></a>
<a class="tile tile-prints abs"><div class="tile-art" role="img" aria-label="Framed geometric prints arranged on a shelf in a room"></div><div class="tile-label"><b>Art Prints</b><small>View More Products</small></div></a>

<h2 class="section-title abs" style="top:910px">New Releases on Fineart</h2>

<div class="product abs" style="left:162px;top:986px"><div class="product-art" role="img" aria-label="Black ink line drawing of swirling forms" style="background:linear-gradient(135deg,#f4f4f4,#9a9a9a 50%,#e8e8e8)"></div><p class="product-name">Lorem ipsum dolor sit amet</p><p class="product-price">£250.00</p></div>
<div class="product abs" style="left:462px;top:986px"><div class="product-art" role="img" aria-label="Sketches of small figures on a pale ground" style="background:linear-gradient(135deg,#f2f2f0,#d6d6d2 60%,#efefed)"></div><p class="product-name">Lorem ipsum dolor sit amet</p><p class="product-price">£450.00</p></div>
<div class="product abs" style="left:763px;top:986px"><div class="product-art" role="img" aria-label="Vertical stripes painting in blue, red, teal and yellow" style="background:linear-gradient(90deg,#3d4a8a,#b84a5e 35%,#5fa7a2 55%,#f0b52e 80%,#f4c542)"></div><p class="product-name">Lorem ipsum dolor sit amet</p><p class="product-price">£550.00</p></div>
<div class="product abs" style="left:162px;top:1275px"><div class="product-art" role="img" aria-label="Teal circular textured artwork on grey" style="background:radial-gradient(circle at 50% 45%,#4f8e8c 0%,#7e9a98 35%,#a7a7a5 70%)"></div><p class="product-name">Lorem ipsum dolor sit amet</p><p class="product-price">£999.00</p></div>
<div class="product abs" style="left:462px;top:1275px"><div class="product-art" role="img" aria-label="Sculptural installation with a red frame and a blue and orange line" style="background:linear-gradient(160deg,#eef0f2,#d9dce2 60%,#c5cad6)"></div><p class="product-name">Lorem ipsum dolor sit amet</p><p class="product-price">£800.00</p></div>
<div class="product abs" style="left:763px;top:1275px"><div class="product-art" role="img" aria-label="Ink drawing of a church tower with orange accents" style="background:linear-gradient(135deg,#f3f1ee,#7a7a78 50%,#e8793c 75%,#f3f1ee)"></div><p class="product-name">Lorem ipsum dolor sit amet</p><p class="product-price">£450.00</p></div>

<a class="btn-more abs">View More Products</a>
<div class="divider abs"></div>

<h2 class="section-title abs" style="top:1675px">Chirpline Feeds</h2>

<article class="post abs" style="left:162px">
  <span class="post-mark"></span>
  <div>
    <p class="post-head"><b>Harwick Moss Fine Art</b> @HarwickMossArt 23 Apr 2012</p>
    <p class="post-body">Harwick Moss Fine Art Spring Sale starts today...<br>10% off everything on our website with promotional code: XYS37QTY...<br>http://hm.art/k3sQ</p>
    <div class="post-meta">
      <span><svg width="12" height="10" viewBox="0 0 12 10"><path d="M5 1 1 5l4 4M1 5h7a3 3 0 0 1 3 3" fill="none" stroke="#999" stroke-width="1.4"/></svg>0 replies</span>
      <span><svg width="14" height="10" viewBox="0 0 14 10"><path d="M3 9V2h7M8 0l2 2-2 2M11 1v7H4M6 10 4 8l2-2" fill="none" stroke="#999" stroke-width="1.3"/></svg>0 retweets</span>
      <span><svg width="11" height="10" viewBox="0 0 11 10"><path d="M5.5 9.5 1 5A2.5 2.5 0 0 1 5.5 1.6 2.5 2.5 0 0 1 10 5Z" fill="#999"/></svg>0 likes</span>
    </div>
  </div>
</article>
<article class="post abs" style="left:635px">
  <span class="post-mark"></span>
  <div>
    <p class="post-head"><b>Harwick Moss Fine Art</b> @HarwickMossArt 23 Apr 2012</p>
    <p class="post-body">Harwick Moss Fine Art Spring Sale starts today...<br>10% off everything on our website with promotional code: XYS37QTY...<br>http://hm.art/k3sQ</p>
    <div class="post-meta">
      <span><svg width="12" height="10" viewBox="0 0 12 10"><path d="M5 1 1 5l4 4M1 5h7a3 3 0 0 1 3 3" fill="none" stroke="#999" stroke-width="1.4"/></svg>0 replies</span>
      <span><svg width="14" height="10" viewBox="0 0 14 10"><path d="M3 9V2h7M8 0l2 2-2 2M11 1v7H4M6 10 4 8l2-2" fill="none" stroke="#999" stroke-width="1.3"/></svg>0 retweets</span>
      <span><svg width="11" height="10" viewBox="0 0 11 10"><path d="M5.5 9.5 1 5A2.5 2.5 0 0 1 5.5 1.6 2.5 2.5 0 0 1 10 5Z" fill="#999"/></svg>0 likes</span>
    </div>
  </div>
</article>

<footer class="site-footer abs">
  <div class="f-col abs" style="left:162px">
    <h4>Help &amp; Info</h4>
    <ul><li>Track Your Order</li><li>Returns</li><li>Shipping Information</li><li>FAQs</li><li>Hollin Gate Credit Card</li><li>Pay Bill Online</li><li>Email Preferences</li><li>International Orders</li><li>Promotion Details</li></ul>
  </div>
  <div class="f-col abs" style="left:363px">
    <h4>Stores</h4>
    <ul><li>Locate a Store</li><li>Store Events</li><li>Free Design Services</li></ul>
    <h4 style="margin-top:26px">Resources</h4>
    <ul><li>What's New</li><li>Gift Cards</li><li>Site Map</li></ul>
  </div>
  <div class="f-col abs" style="left:543px">
    <h4>Our Company</h4>
    <ul><li>About Us</li><li>Environmental Commitment</li><li>Careers</li><li>Press</li><li>Legal Statement</li><li>Privacy Policy</li><li>Terms &amp; Conditions</li></ul>
  </div>
  <div class="f-col abs" style="left:746px">
    <h4>Newsletter</h4>
    <div class="newsletter"><span class="field">Email Address:</span><span class="go">SIGN UP</span></div>
    <h4 style="margin-top:22px;margin-bottom:0">Follow US</h4>
    <div class="social"><span></span><span></span><span></span><span></span></div>
  </div>
  <div class="legal-rule abs"></div>
  <p class="legal abs">Privacy Policy<span class="sep">|</span>Terms of Use<span class="sep">|</span>Site Map<span class="sep">|</span>Live Chat<span class="sep">|</span>© 2017 Harwick Moss Fine Art . All Rights Reserved</p>
</footer>

</body>
</html>
```